Veltrane Group Business Card Design

The CEO is looking for a new trendy look for his business card.
You can stay with current branding or come up with something new/creative. It can be 3D, including Medical Office buildings. You can use our logo in a variety of colors. Please include name, title, company name, company website, email address, cell number

Target Market(s)

Real Estate Development and Construction

Industry/Entity Type

Health care real estate

Contact Information for Business Card

Rohesh Kamdar, CEO M-604.781.2249 E-roheshkamdar@veltrane.com Address:4180 Lindqvist Ave, Tampa, FL 33482 www.veltrane.com

Font styles to use
Other font styles liked:
• Be creative

Requirements
Must have
• Creative, trendy look
Nice to have
• Please go to our website to get a feel- www. veltrane.com
Should not have
• small fonts

```html
<!DOCTYPE html>
<html lang="en">
<head>
<meta charset="utf-8">
<title>Veltrane Group Business Card</title>
<link href="https://fonts.googleapis.com/css2?family=Poppins:wght@400;700&display=swap" rel="stylesheet">
<style>
  :root {
    --brand-red: #b21f2b;
    --brand-red-deep: #9a1a25;
    --brand-navy: #1b2f52;
    --ink: #222222;
    --paper: #ffffff;
    --backdrop: #9b9b9b;
  }
  * { margin: 0; padding: 0; box-sizing: border-box; }
  html, body { width: 1093px; height: 1200px; overflow: hidden; }
  body {
    position: relative;
    background: var(--backdrop);
    font-family: 'Poppins', sans-serif;
  }
  .card {
    position: absolute;
    left: 264px;
    width: 579px;
    height: 357px;
  }
  .card-front { top: 226px; background: var(--paper); }
  .card-back { top: 620px; width: 582px; background: var(--brand-red); }

  .edge-band { position: absolute; left: 0; top: 0; width: 16px; height: 357px; }

  .holder { position: absolute; left: 32px; top: 34px; }
  .holder-name {
    font-weight: 700; font-size: 23px; line-height: 27px;
    color: var(--brand-red); letter-spacing: 0.2px;
  }
  .holder-title {
    font-weight: 400; font-size: 16px; line-height: 18px;
    color: var(--brand-navy);
  }

  .brand-name {
    position: absolute; right: 27px; top: 30px;
    font-weight: 700; font-size: 30px; line-height: 36px;
    color: var(--brand-red); white-space: nowrap;
  }

  .contact-list {
    position: absolute; left: 32px; top: 268px;
    list-style: none;
  }
  .contact-item {
    display: flex; align-items: center; gap: 7px;
    height: 21px;
    font-size: 17.5px; color: var(--ink);
  }
  .contact-icon { width: 15px; height: 15px; flex: none; }

  .address {
    position: absolute; right: 27px; top: 289px;
    text-align: right; font-size: 17.5px; line-height: 21px; color: var(--ink);
  }

  .back-brand {
    position: absolute; left: 0; right: 0; top: 145px;
    text-align: center;
    font-weight: 700; font-size: 52px; line-height: 64px;
    color: var(--brand-red-deep); white-space: nowrap;
  }
</style>
</head>
<body>

<section class="card card-front" aria-label="Business card front">
  <svg class="edge-band" viewBox="0 0 16 357" aria-hidden="true">
    <rect x="0" y="0" width="16" height="357" fill="var(--brand-red)"/>
    <polygon points="0,0 16,0 16,68 0,63" fill="var(--brand-navy)"/>
    <line x1="0" y1="64" x2="16" y2="69" stroke="var(--paper)" stroke-width="2"/>
  </svg>

  <div class="holder">
    <p class="holder-name">Rohesh Kamdar</p>
    <p class="holder-title">CEO</p>
  </div>

  <p class="brand-name">Veltrane Group</p>

  <ul class="contact-list">
    <li class="contact-item">
      <svg class="contact-icon" viewBox="0 0 16 16" aria-hidden="true">
        <path d="M3.2 1.5l2.3 2.6-1.3 1.6c.9 2 2.4 3.5 4.3 4.5l1.6-1.3 2.6 2.3-1.5 2.3C6.4 13.3 2.6 9.4 1 4.5z" fill="var(--brand-red)"/>
        <path d="M9 4.2a3 3 0 0 1 2.8 2.8M9 1.6a5.6 5.6 0 0 1 5.4 5.4" stroke="var(--brand-red)" stroke-width="1.4" fill="none"/>
      </svg>
      <span>604.781.2249</span>
    </li>
    <li class="contact-item">
      <svg class="contact-icon" viewBox="0 0 16 16" aria-hidden="true">
        <rect x="0.5" y="3" width="15" height="10" fill="var(--brand-red)"/>
        <path d="M0.5 3.5L8 9l7.5-5.5M0.5 12.5l5.5-4.5M15.5 12.5L10 8" stroke="var(--paper)" stroke-width="1" fill="none"/>
      </svg>
      <span>roheshkamdar@veltrane.com</span>
    </li>
    <li class="contact-item">
      <svg class="contact-icon" viewBox="0 0 16 16" aria-hidden="true">
        <g stroke="var(--brand-red)" stroke-width="1.3" fill="none">
          <circle cx="8" cy="8" r="6.8"/>
          <ellipse cx="8" cy="8" rx="3" ry="6.8"/>
          <path d="M1.2 8h13.6M2.2 4.6h11.6M2.2 11.4h11.6M8 1.2v13.6"/>
        </g>
      </svg>
      <span>www.veltrane.com</span>
    </li>
  </ul>

  <address class="address" style="font-style: normal;">
    4180 Lindqvist Ave, Tampa<br>FL 33482
  </address>
</section>

<section class="card card-back" aria-label="Business card back">
  <p class="back-brand">Veltrane Group</p>
</section>

</body>
</html>
```